Business Card Design for Marketing Firm

Looking for business card design for higher end marketing firm. Clean but impressionable/trendy. We are a marketing firm that represents manufacturers in the foodservice equipment and supply industry. Our customers are end users such has hotels, restaurants, country clubs, convention centers and casinos as well as distributors of restaurants supplies and equipment, and manufacturers of foodservice equipment and supplies.
Target Market(s)
Hotels, Restaurants, Supply & Equipment Distributors, Foodservice Manufacturers
Industry/Entity Type
Foodservice/Hospitality
Contact Information for Business Card
Name, Title, Contact Number, Email, Website, Social Media, Address
Requirements
Must have
- Clean & Simple but Serious and Impressionable

```html
<!DOCTYPE html>
<html lang="en">
<head>
<meta charset="utf-8">
<title>Harbor Table Reps – Business Card</title>
<link href="https://fonts.googleapis.com/css2?family=EB+Garamond:wght@400;600;700&display=swap" rel="stylesheet">
<style>
  :root {
    --ink-blue: #05047f;
    --paper: #ffffff;
    --text-grey: #3a3a3a;
    --backdrop: #e6e6e9;
  }
  * { box-sizing: border-box; margin: 0; padding: 0; }
  html, body {
    width: 1200px; height: 821px; overflow: hidden;
    background: var(--backdrop);
    font-family: "EB Garamond", Georgia, serif;
  }
  .sheet {
    width: 1200px; height: 821px;
    display: flex; align-items: center; justify-content: center; gap: 40px;
  }
  .card {
    width: 540px; height: 309px; position: relative;
    box-shadow: 0 6px 18px rgba(0,0,0,.18);
  }
  .card--front { background: var(--paper); }
  .card--back { background: var(--ink-blue); display: flex; align-items: center; justify-content: center; }
  .card__frame {
    position: absolute; inset: 16px;
    border: 2px solid var(--ink-blue);
  }
  .contact {
    position: absolute; right: 262px; top: 62px;
    text-align: right; color: var(--text-grey);
    font-size: 14px; line-height: 1.32;
  }
  .contact__name {
    color: var(--ink-blue); font-weight: 700;
    font-size: 24px; letter-spacing: .04em; line-height: 1.05;
  }
  .contact__title { font-size: 17px; letter-spacing: .03em; }
  .contact__company { color: var(--ink-blue); font-size: 15px; margin-bottom: 1px; }
  .contact__row { display: flex; align-items: center; justify-content: flex-end; gap: 6px; }
  .contact__row--spaced { margin-top: 4px; }
  .icon { width: 11px; height: 11px; flex: none; }
  .wordmark {
    position: absolute; left: 300px; top: 112px;
    color: var(--ink-blue); font-weight: 600;
    font-size: 34px; line-height: 1.0; letter-spacing: .02em;
    text-align: left;
  }
  .wordmark--back {
    position: static; color: var(--paper);
    font-size: 44px; text-align: center; letter-spacing: .06em;
  }
</style>
</head>
<body>
<main class="sheet">
  <section class="card card--front" aria-label="Business card front">
    <div class="card__frame"></div>
    <div class="contact">
      <p class="contact__name">JON HALE</p>
      <p class="contact__title">Founder &amp; CEO</p>
      <p class="contact__company">Harbor Table Reps</p>
      <p>418 Crestwood Lane, Ste 12</p>
      <p>Milford, CT 06460</p>
      <p class="contact__row contact__row--spaced">(555) 210-4378
        <svg class="icon" viewBox="0 0 24 24" aria-hidden="true"><path fill="#05047f" d="M6.6 10.8a15 15 0 0 0 6.6 6.6l2.2-2.2c.3-.3.7-.4 1-.2 1.1.4 2.3.6 3.6.6.6 0 1 .4 1 1V20c0 .6-.4 1-1 1C10.6 21 3 13.4 3 4c0-.6.4-1 1-1h3.5c.6 0 1 .4 1 1 0 1.3.2 2.5.6 3.6.1.3 0 .7-.2 1z"/></svg>
      </p>
      <p class="contact__row">hello@harbortablereps.com
        <svg class="icon" viewBox="0 0 24 24" aria-hidden="true"><rect x="2" y="5" width="20" height="14" fill="#05047f"/><path d="M2 5l10 8 10-8" fill="none" stroke="#fff" stroke-width="1.6"/></svg>
      </p>
      <p class="contact__row">harbortablereps.com
        <svg class="icon" viewBox="0 0 24 24" aria-hidden="true"><circle cx="12" cy="12" r="10" fill="#05047f"/><path d="M2 12h20M12 2c3 3 3 17 0 20M12 2c-3 3-3 17 0 20" fill="none" stroke="#fff" stroke-width="1.4"/></svg>
      </p>
    </div>
    <p class="wordmark">Harbor<br>Table</p>
  </section>

  <section class="card card--back" aria-label="Business card back">
    <p class="wordmark wordmark--back">HARBOR TABLE<br>REPS</p>
  </section>
</main>
</body>
</html>
```